Need Business Card for our Real Estate Business with Sales Executive's Picture

PANTONE 484 C ( RED)

PANTONE 2766 C ( BLUE

Industry/Entity Type

Real Estate

Contact Information for Business Card

Name, Mobile, email, & picture of Person
Agency Phone, address, Web address

Requirements
Must have
• Our Logo Colours, Agent Picture,

```html
<!DOCTYPE html>
<html lang="en">
<head>
<meta charset="utf-8">
<title>Dunmore Real Estate – Business Card</title>
<link href="https://fonts.googleapis.com/css2?family=Open+Sans:wght@400;600&display=swap" rel="stylesheet">
<style>
  :root {
    --backdrop: #c9ccd1;
    --paper: #ffffff;
    --navy: #03163a;
    --slate: #676b88;
    --ink: #444649;
    --rule: #555555;
    --photo-top: #2b4a8a;
    --photo-bottom: #13234a;
  }
  * { box-sizing: border-box; margin: 0; padding: 0; }
  html, body {
    width: 1200px; height: 1000px; overflow: hidden;
    background: var(--backdrop);
    font-family: "Open Sans", Arial, sans-serif;
    color: var(--ink);
  }
  .card {
    position: absolute;
    overflow: hidden;
    background: var(--paper);
  }
  .card-front { left: 261px; top: 85px; width: 680px; height: 387px; }
  .card-back  { left: 261px; top: 525px; width: 682px; height: 388px; background: var(--navy); }
  .card-shape { position: absolute; inset: 0; width: 100%; height: 100%; }

  .agent-photo {
    position: absolute; left: 35px; top: 37px; width: 124px; height: 175px;
    background: linear-gradient(180deg, var(--photo-top), var(--photo-bottom));
  }
  .brand-name {
    position: absolute; font-weight: 600; letter-spacing: 2px; text-align: center;
  }
  .front-brand {
    left: 243px; width: 200px; top: 74px; font-size: 22px; color: var(--navy);
  }
  .agent-name {
    position: absolute; left: 150px; width: 380px; top: 140px;
    text-align: center; font-size: 24px; line-height: 1.2;
  }
  .agent-role {
    position: absolute; left: 150px; width: 370px; top: 174px;
    text-align: center; font-size: 19px;
  }
  .divider {
    position: absolute; left: 26px; top: 211px; width: 564px; height: 2px; background: var(--rule);
  }
  .agency-address {
    position: absolute; left: 150px; width: 378px; top: 222px;
    text-align: center; font-size: 19px;
  }
  .contact-list { position: absolute; left: 40px; top: 267px; list-style: none; }
  .contact-item {
    display: flex; align-items: center; height: 31px; font-size: 17px;
  }
  .contact-icon { width: 20px; height: 20px; margin-right: 13px; }

  .back-brand {
    left: 0; width: 100%; top: 170px; font-size: 46px; color: var(--paper); letter-spacing: 4px;
  }
</style>
</head>
<body>

<section class="card card-front">
  <svg class="card-shape" viewBox="0 0 680 387" preserveAspectRatio="none" aria-hidden="true">
    <path d="M510,0 C560,40 640,150 612,225 C588,292 530,350 508,387 L680,387 L680,0 Z" fill="var(--slate)"/>
    <path d="M548,0 C605,60 640,150 622,232 C604,302 562,352 550,387 L680,387 L680,0 Z" fill="var(--navy)"/>
  </svg>

  <div class="agent-photo" role="img" aria-label="Portrait photo of the sales executive"></div>
  <div class="brand-name front-brand">DUNMORE</div>

  <h1 class="agent-name" style="font-weight:400">Name of Sales Executive's</h1>
  <p class="agent-role">Sales Executive</p>
  <div class="divider"></div>
  <p class="agency-address">address of Dunmore Real Estate</p>

  <ul class="contact-list">
    <li class="contact-item">
      <svg class="contact-icon" viewBox="0 0 20 20" aria-hidden="true">
        <circle cx="10" cy="10" r="8" fill="none" stroke="var(--ink)" stroke-width="1.5"/>
        <path d="M7,6 C6,8 8,13 12,14 L13.5,12.5 L12,11 L11,12 C9.5,11.3 8.7,10.5 8,9 L9,8 L7.8,6 Z" fill="var(--ink)"/>
      </svg>
      mobile / agency phone
    </li>
    <li class="contact-item">
      <svg class="contact-icon" viewBox="0 0 20 20" aria-hidden="true">
        <rect x="2" y="5" width="16" height="11" fill="var(--ink)"/>
        <path d="M2.5,5.5 L10,11 L17.5,5.5" fill="none" stroke="var(--paper)" stroke-width="1.2"/>
      </svg>
      dunmore@email.com
    </li>
    <li class="contact-item">
      <svg class="contact-icon" viewBox="0 0 20 20" aria-hidden="true">
        <g fill="none" stroke="var(--ink)" stroke-width="1.4">
          <circle cx="10" cy="10" r="8"/>
          <ellipse cx="10" cy="10" rx="3.5" ry="8"/>
          <line x1="2" y1="10" x2="18" y2="10"/>
          <line x1="3.5" y1="6" x2="16.5" y2="6"/>
          <line x1="3.5" y1="14" x2="16.5" y2="14"/>
        </g>
      </svg>
      www.webaddress.com
    </li>
  </ul>
</section>

<section class="card card-back">
  <svg class="card-shape" viewBox="0 0 682 388" preserveAspectRatio="none" aria-hidden="true">
    <path d="M0,187 C130,160 230,337 341,337 C452,337 552,160 682,187 L682,388 L0,388 Z" fill="var(--slate)"/>
    <path d="M0,255 C120,230 230,347 341,347 C452,347 560,230 682,255 L682,388 L0,388 Z" fill="var(--paper)"/>
  </svg>
  <div class="brand-name back-brand">DUNMORE</div>
</section>

</body>
</html>
```